International Manufacturing Business Needs A Heavy Hitting Wordpress Design!

We need wordpress template designs for a new website for our UK based International company Dalvesham Engineering Ltd. We manufacture and supply steel security doors and window units. We would like designs that feature the black and yellow industrial "stripes" that can be seen at our current site www.dalvoportals.com. The final design should communicate strength, power and weight to represent the quality of the products and the security that they provide.

It feels like we need 3 different types of page to be able to be created as per the current website at www.dalvosafeportals.com.

Homepage
Products/Accessories
Leadtimes/Downloads/Contact

It may be that 3 different page types can be created with one template. I'm totally open to this.

I don't like the way that the site currently handles product images, nobody wants to click on even thumbnail to see the product. http://dalvosafeportals.com/products/personnel-doors/

Totally open to suggestions on layout to enable the feeling outlined in the brief above.

Please ask if anything is not clear or you need answers to drill down on specifics.

Sick

Target Market(s)

Businesses that buy steel doors

Font styles to use
Sans Serif
Other font styles liked:
• Copperplate Gothic Bold - For Company Name but we are open to suggestions

Colors

Designer to choose colors to be used in the design.

Requirements
Must have
• Professional looking, clean design
• Conveys strength, power and weight to represent the quality of the products, the characteristics of steel and the security that they provide.
• Incorporates black and yellow stripes of our branding
• Ability to create pages with content as seen at www.dalvosafeportals.com
• A better way of showing the product images
Nice to have
• If possible. a design that gives off the feeling that not only do we supply the products we also make them in house too. I don't know what this looks like but a way of differentiating between a supply only business and one that manufacturers the product too.
Should not have
• We don't like the current thumbnail method of showing the product images

```html
<!DOCTYPE html>
<html lang="en">
<head>
<meta charset="utf-8">
<title>Dalvesham Engineering Ltd – Steel Security Doors</title>
<link rel="stylesheet" href="https://fonts.googleapis.com/css2?family=Roboto:wght@400;500;700&family=Roboto+Condensed:wght@400;700&display=swap">
<style>
:root{
  --green:#4c9a6b;
  --green-dark:#3d8459;
  --yellow:#f3c317;
  --black:#0f0f0f;
  --ink:#222;
  --muted:#555;
  --light:#f2f2f2;
  --nav-active:#2f2f2f;
}
*{margin:0;padding:0;box-sizing:border-box}
html,body{width:1200px;height:3237px;overflow:hidden}
body{font-family:"Roboto",Arial,sans-serif;color:var(--ink);background:#fff;position:relative}
.abs{position:absolute}
.hazard{position:absolute;left:0;width:1200px;height:20px;
  background:repeating-linear-gradient(-45deg,var(--yellow) 0 14px,var(--black) 14px 28px)}
.hazard.thin{height:12px}

/* header */
.site-header{top:0;left:0;width:1200px;height:123px}
.brand{left:133px;top:30px;display:flex;align-items:center;gap:14px}
.brand-mark{width:34px;height:64px;background:var(--green)}
.brand-name{font-family:"Roboto Condensed",Arial,sans-serif;font-weight:700;color:#2b2b2b;line-height:1}
.brand-name .l1{display:block;font-size:40px;letter-spacing:1px}
.brand-name .l2{display:block;font-size:19px;letter-spacing:3.2px;margin-top:4px}
.contact-top{left:562px;top:38px;display:flex;gap:12px}
.contact-top svg{margin-top:4px}
.contact-top .phone{font-size:19px;font-weight:500;color:#222}
.contact-top .mail{font-size:14px;color:#444;margin-top:5px}
.search{left:832px;top:45px;width:236px;height:34px;border:1px solid #cfcfcf;border-radius:17px;
  font-size:11px;color:#999;padding:10px 16px}
.search svg{position:absolute;right:12px;top:8px}

.main-nav{top:123px;left:0;width:1200px;height:47px;background:var(--green);}
.main-nav ul{list-style:none;display:flex;position:absolute;left:130px;top:0;height:47px}
.main-nav li{font-family:"Roboto",sans-serif;font-weight:500;font-size:14px;color:#fff;
  padding:0 19px;line-height:47px;letter-spacing:.4px}
.main-nav li.active{background:var(--nav-active)}

/* hero */
.hero{top:170px;left:0;width:1200px;height:545px}
.hero-photo{position:absolute;inset:0;
  background:linear-gradient(90deg,#0b0b0a 0%,#1a1a16 40%,#c9a417 52%,#f0d02a 57%,#2d2a1f 60%,#9ea186 70%,#e9ece4 85%,#c9cfc0 100%)}
.hero-title{left:103px;top:147px;font-family:"Roboto Condensed",sans-serif;font-weight:700;
  font-size:60px;line-height:64px;color:#fff;letter-spacing:.5px}
.hero-title .accent{color:var(--yellow)}
.dots{left:103px;top:361px;display:flex;gap:9px}
.dots span{width:15px;height:15px;border-radius:50%;border:2px solid #fff}
.dots span.on{background:var(--yellow);border-color:var(--yellow)}

/* what we do */
.about{top:735px;left:0;width:1200px;height:575px}
.about-photo{left:138px;top:150px;width:238px;height:238px;border-radius:50%;border:9px solid var(--green);
  background:radial-gradient(circle at 55% 45%,#e8e2b0 0%,#c0b35a 30%,#8a8a88 55%,#2a3a30 100%);
  width:364px;height:364px;left:137px;top:148px}
.about h2{left:557px;top:88px;font-family:"Roboto",sans-serif;font-weight:500;font-size:38px;color:#1a1a1a;letter-spacing:.5px}
.about ul{left:557px;top:152px;width:500px;list-style:none}
.about li{position:relative;padding-left:24px;font-size:12.5px;line-height:19.5px;color:#333;margin-bottom:11.5px}
.about li svg{position:absolute;left:0;top:3px}

/* features */
.features{top:1310px;left:0;width:1200px;height:550px;background:#111}
.features-photo{left:0;top:0;width:600px;height:550px;
  background:linear-gradient(90deg,#c9b98a 0%,#a89a6a 25%,#b22020 30%,#c8241f 45%,#7a1512 62%,#1c1c1c 100%)}
.features-fade{left:480px;top:0;width:260px;height:550px;background:linear-gradient(90deg,rgba(17,17,17,0),#111)}
.feature{left:645px;width:460px;display:flex;gap:22px}
.feature .ico{width:66px;height:66px;border-radius:50%;background:var(--green);flex:none;display:flex;align-items:center;justify-content:center}
.feature h3{font-size:15px;font-weight:500;color:#fff;margin-top:6px;letter-spacing:.3px}
.feature p{font-size:11px;line-height:17px;color:#ddd;margin-top:7px;width:270px}

/* products */
.products{top:1880px;left:0;width:1200px;height:695px}
.products h2{left:0;width:1200px;text-align:center;top:88px;font-size:34px;font-weight:400;color:#1a1a1a}
.products h2 b{font-weight:700}
.card{top:180px;width:298px;height:390px;text-align:center}
.card.featured{background:#eeeeee;box-shadow:0 3px 8px rgba(0,0,0,.25)}
.card .pic{height:182px;border-radius:10px 10px 0 0;position:relative;overflow:hidden}
.card .pic svg{position:absolute;left:0;bottom:0}
.card h3{font-size:18px;font-weight:500;color:#1e1e1e;margin-top:22px;letter-spacing:.2px}
.card p{font-size:11.5px;line-height:22px;color:#333;margin:12px auto 0;width:268px}
.card .btn{position:absolute;left:50%;transform:translateX(-50%);top:346px;width:108px;height:30px;border:1.5px solid #333;
  border-radius:15px;font-size:10px;font-weight:500;color:#222;line-height:27px}
.arrow{top:2245px}

/* partners */
.partners{top:2575px;left:0;width:1200px;height:140px;background:var(--light)}
.partner{top:55px;height:30px;background:#a8a8a8;border-radius:4px}

/* footer */
.footer{top:2735px;left:0;width:1200px;height:502px;background:var(--black);color:#fff}
.footer h4{top:80px;font-size:22px;font-weight:500;letter-spacing:.3px;font-family:"Roboto",sans-serif}
.quick{left:130px;top:125px;list-style:none}
.quick li{font-size:12.5px;line-height:24px;color:#ddd}
.quick li::before{content:"›";margin-right:12px;color:#ddd}
.contact-list{left:347px;top:125px;font-size:11.5px;line-height:18px;color:#ddd}
.contact-list .row{display:flex;gap:12px;margin-bottom:14px}
.contact-list svg{flex:none;margin-top:3px}
.quote-intro{left:630px;top:123px;font-size:13.5px;color:#eee}
.field{height:41px;border:1px solid #888;font-size:10.5px;color:#ddd;padding:14px 14px}
.submit{background:var(--green);color:#fff;font-size:14px;font-weight:700;text-align:center;line-height:41px;letter-spacing:.5px}
.social{left:527px;top:385px;display:flex;gap:6px}
.social span{width:24px;height:24px;border:1.5px solid #ccc;border-radius:50%}
.copy{left:0;width:1200px;text-align:center;top:446px;font-size:11.5px;color:#ddd}
</style>
</head>
<body>

<!-- header -->
<header class="site-header abs">
  <div class="hazard thin" style="top:0"></div>
  <div class="brand abs">
    <span class="brand-mark"></span>
    <span class="brand-name"><span class="l1">DALVESHAM</span><span class="l2">ENGINEERING LTD.</span></span>
  </div>
  <div class="contact-top abs">
    <svg width="24" height="30" viewBox="0 0 24 30"><path d="M5 2c2 0 3 5 3 6s-3 2-2 5 4 8 6 9 3-2 4-2 5 2 5 4-3 5-6 5C9 29 1 17 1 8c0-3 2-6 4-6z" fill="var(--green)"/></svg>
    <div><div class="phone">+44 (0)1632 960 300</div><div class="mail">sales@dalvoportals.com</div></div>
  </div>
  <div class="search abs">Search here
    <svg width="16" height="16" viewBox="0 0 16 16"><circle cx="6.5" cy="6.5" r="5" fill="none" stroke="#888" stroke-width="1.6"/><line x1="10.3" y1="10.3" x2="15" y2="15" stroke="#888" stroke-width="1.8"/></svg>
  </div>
</header>

<nav class="main-nav abs">
  <ul>
    <li class="active">HOME</li><li>PRODUCTS</li><li>ACCESSORIES</li><li>DELIVERY &amp; LEAD TIMES</li><li>DOWNLOADS</li><li>BLOG</li><li>CONTACT</li>
  </ul>
</nav>

<!-- hero -->
<section class="hero abs">
  <div class="hero-photo" role="img" aria-label="Close-up of a chrome push-bar handle on a yellow steel fire exit door opening onto a bright room"></div>
  <h1 class="hero-title abs">DALVESHAM<br><span class="accent">STEEL FIRE</span><br>EXIT DOORS</h1>
  <div class="dots abs"><span class="on"></span><span></span><span></span></div>
</section>
<div class="hazard" style="top:715px"></div>

<!-- what we do -->
<section class="about abs">
  <div class="about-photo abs" role="img" aria-label="Multi-bolt steel door lock with keyhole"></div>
  <h2 class="abs">WHAT WE DO</h2>
  <ul class="abs">
    <li><svg width="12" height="12" viewBox="0 0 12 12"><circle cx="6" cy="6" r="6" fill="var(--green)"/><path d="M5 3.5l2.5 2.5L5 8.5" stroke="#fff" stroke-width="1.5" fill="none"/></svg>Dalvesham security doors combine a high level of security with exceptional value.</li>
    <li><svg width="12" height="12" viewBox="0 0 12 12"><circle cx="6" cy="6" r="6" fill="var(--green)"/><path d="M5 3.5l2.5 2.5L5 8.5" stroke="#fff" stroke-width="1.5" fill="none"/></svg>Our superior quality and proven reliability has made us the first choice for a wide range of companies no matter what their requirement or application.</li>
    <li><svg width="12" height="12" viewBox="0 0 12 12"><circle cx="6" cy="6" r="6" fill="var(--green)"/><path d="M5 3.5l2.5 2.5L5 8.5" stroke="#fff" stroke-width="1.5" fill="none"/></svg>All of our products are designed and manufactured to the highest specification, combine this with a rigorous quality control system and an extensive after-sales service and it is easy to see why we are seen as industry leaders.</li>
    <li><svg width="12" height="12" viewBox="0 0 12 12"><circle cx="6" cy="6" r="6" fill="var(--green)"/><path d="M5 3.5l2.5 2.5L5 8.5" stroke="#fff" stroke-width="1.5" fill="none"/></svg>We place particular emphasis on continuous development and twelve years experience ensures that we are always ahead of the competition and that we can react quickly to customer's requirements.</li>
    <li><svg width="12" height="12" viewBox="0 0 12 12"><circle cx="6" cy="6" r="6" fill="var(--green)"/><path d="M5 3.5l2.5 2.5L5 8.5" stroke="#fff" stroke-width="1.5" fill="none"/></svg>Each and every Dalvesham product is subject to our fifty point quality control process before it is dispatched.</li>
    <li><svg width="12" height="12" viewBox="0 0 12 12"><circle cx="6" cy="6" r="6" fill="var(--green)"/><path d="M5 3.5l2.5 2.5L5 8.5" stroke="#fff" stroke-width="1.5" fill="none"/></svg>Dalvesham have forged a reputation for affordable, high quality steel doors.</li>
  </ul>
</section>

<!-- features -->
<section class="features abs">
  <div class="features-photo abs" role="img" aria-label="Red steel security door with chrome handle, key and multi-point lock"></div>
  <div class="features-fade abs"></div>
  <div class="feature abs" style="top:96px">
    <div class="ico"><svg width="30" height="30" viewBox="0 0 30 30"><rect x="4" y="6" width="18" height="18" rx="2" fill="none" stroke="#fff" stroke-width="2"/><path d="M13 17l11-11 3 3-11 11h-3z" fill="#fff"/></svg></div>
    <div><h3>FREE ESTIMATES</h3><p>Lorem ipsum dolor sit amet, consectetur adipiscing elit, sed do eiusmod tempor incididunt</p></div>
  </div>
  <div class="feature abs" style="top:200px">
    <div class="ico"><svg width="32" height="24" viewBox="0 0 32 24"><rect x="1" y="3" width="18" height="14" fill="#fff"/><path d="M20 7h6l4 5v5H20z" fill="#fff"/><circle cx="8" cy="19" r="3" fill="#fff" stroke="var(--green)" stroke-width="1.5"/><circle cx="24" cy="19" r="3" fill="#fff" stroke="var(--green)" stroke-width="1.5"/></svg></div>
    <div><h3>DELIVERY</h3><p>We use a select range of haulage companies to deliver our products, they have a proven record of delivering safely and on time.</p></div>
  </div>
  <div class="feature abs" style="top:305px">
    <div class="ico"><svg width="30" height="30" viewBox="0 0 30 30"><circle cx="15" cy="15" r="12" fill="none" stroke="#fff" stroke-width="2.5"/><path d="M15 8v7l5 3" stroke="#fff" stroke-width="2.5" fill="none"/></svg></div>
    <div><h3>LEAD TIMES</h3><p>Lorem ipsum dolor sit amet, consectetur adipiscing elit, sed do eiusmod tempor incididunt</p></div>
  </div>
  <div class="feature abs" style="top:409px">
    <div class="ico"><svg width="22" height="30" viewBox="0 0 22 30"><path d="M11 1C5 1 1 5.5 1 11c0 7 10 18 10 18s10-11 10-18C21 5.5 17 1 11 1z" fill="#fff"/><circle cx="11" cy="11" r="4" fill="var(--green)"/></svg></div>
    <div><h3>VISIT US TODAY!</h3><p>Lorem ipsum dolor sit amet, consectetur adipiscing elit, sed do eiusmod tempor incididunt</p></div>
  </div>
</section>
<div class="hazard" style="top:1860px"></div>

<!-- products -->
<section class="products abs">
  <h2 class="abs">OUR <b>PRODUCTS</b></h2>

  <article class="card abs" style="left:131px">
    <div class="pic" role="img" aria-label="Red personnel door with louvred vent and lever handle" style="background:linear-gradient(135deg,#d22a2a,#9c1414)">
      <svg width="298" height="30" viewBox="0 0 298 30" preserveAspectRatio="none"><path d="M0 8Q149 38 298 8V30H0z" fill="#fff"/><path d="M0 8Q149 38 298 8" stroke="var(--green)" stroke-width="4" fill="none"/></svg>
    </div>
    <h3>PERSONNEL DOORS</h3>
    <p>Dalvesham steel security doors are the ideal solution for a wide range of applications in which security, quality and cost are all essential requirements.</p>
    <span class="btn">READ MORE ⊕</span>
  </article>

  <article class="card featured abs" style="left:451px">
    <div class="pic" role="img" aria-label="Yellow fire exit door with chrome push-bar" style="background:linear-gradient(90deg,#111 0%,#2a2a22 45%,#d9b21a 60%,#f1cf2a 75%,#1a1a14 100%)">
      <svg width="298" height="30" viewBox="0 0 298 30" preserveAspectRatio="none"><path d="M0 8Q149 38 298 8V30H0z" fill="#eeeeee"/><path d="M0 8Q149 38 298 8" stroke="var(--green)" stroke-width="4" fill="none"/></svg>
    </div>
    <h3>FIRE EXIT DOORS</h3>
    <p>Dalvesham steel fire exit doors are designed and manufactured to the same high standards as the multi-locking personnel doors.</p>
    <span class="btn">READ MORE ⊕</span>
  </article>

  <article class="card abs" style="left:771px">
    <div class="pic" role="img" aria-label="Blank steel door with multi-bolt lock" style="background:linear-gradient(90deg,#6b5a48,#a89888 45%,#d6cfc4 60%,#5a4a3a)">
      <svg width="298" height="30" viewBox="0 0 298 30" preserveAspectRatio="none"><path d="M0 8Q149 38 298 8V30H0z" fill="#fff"/><path d="M0 8Q149 38 298 8" stroke="var(--green)" stroke-width="4" fill="none"/></svg>
    </div>
    <h3>BLANK DOORS</h3>
    <p>Dalvesham steel security doors are the ideal solution for a wide range of applications in which security, quality and cost are all essential requirements.</p>
    <span class="btn">READ MORE ⊕</span>
  </article>
</section>
<svg class="arrow abs" style="left:68px" width="24" height="48" viewBox="0 0 24 48"><path d="M20 2L4 24l16 22" stroke="#555" stroke-width="2.5" fill="none"/></svg>
<svg class="arrow abs" style="left:1104px" width="24" height="48" viewBox="0 0 24 48"><path d="M4 2l16 22L4 46" stroke="#555" stroke-width="2.5" fill="none"/></svg>

<!-- partners -->
<section class="partners abs" aria-label="Partner brands">
  <div class="partner abs" style="left:178px;width:62px"></div>
  <div class="partner abs" style="left:290px;width:106px"></div>
  <div class="partner abs" style="left:451px;width:86px"></div>
  <div class="partner abs" style="left:605px;width:100px"></div>
  <div class="partner abs" style="left:783px;width:78px"></div>
  <div class="partner abs" style="left:928px;width:110px"></div>
</section>
<div class="hazard" style="top:2715px"></div>

<!-- footer -->
<footer class="footer abs">
  <h4 class="abs" style="left:130px">QUICK LINKS</h4>
  <ul class="quick abs">
    <li>Home</li><li>Products</li><li>Accessories</li><li>Delivery &amp; Lead Times</li><li>Downloads</li><li>Contact</li>
  </ul>

  <h4 class="abs" style="left:347px">CONTACT US</h4>
  <div class="contact-list abs">
    <div class="row"><svg width="11" height="14" viewBox="0 0 11 14"><path d="M5.5 0C2.5 0 0 2.3 0 5.3 0 9 5.5 14 5.5 14S11 9 11 5.3C11 2.3 8.5 0 5.5 0z" fill="#fff"/><circle cx="5.5" cy="5.3" r="2" fill="#000"/></svg><div>Dalvesham Engineering Ltd.<br>Harlow Mill Ferry Lane<br>Brackenby Hull Uk HU9 7QX</div></div>
    <div class="row"><svg width="12" height="12" viewBox="0 0 12 12"><path d="M2.5 0c1 0 1.5 2.5 1.5 3S2.5 4 3 5.5s2 3.5 3 4 1.5-1 2-1 3 1 3 2-1.5 1.5-3 1.5C4.5 12 0 7 0 3 0 1.5 1.5 0 2.5 0z" fill="#fff"/></svg><div>Toll Free: +44 (0) 1632 960300<br>Fax: +44 (0) 1632 960400</div></div>
    <div class="row" style="margin-top:6px"><svg width="12" height="10" viewBox="0 0 12 10"><rect width="12" height="10" fill="#fff"/><path d="M0 0l6 5 6-5" stroke="#000" fill="none"/></svg><div>E-Mail: info@dalvoportals.com</div></div>
  </div>

  <h4 class="abs" style="left:630px">GET A QUOTE</h4>
  <p class="quote-intro abs">Alternatively You Can Fill In The Following Contact Form:</p>
  <div class="field abs" style="left:630px;top:165px;width:212px">Name</div>
  <div class="field abs" style="left:856px;top:165px;width:212px">E - Mail</div>
  <div class="field abs" style="left:630px;top:215px;width:212px">Phone No</div>
  <div class="submit abs" style="left:856px;top:215px;width:212px;height:41px">SUBMIT</div>

  <div class="social abs"><span></span><span></span><span></span><span></span></div>
  <p class="copy abs">© 2018 Dalvesham Engineering Ltd. All Rights Reserved.</p>
</footer>

</body>
</html>
```